co working space / serviced office/ business centre

Brevlo - brevlo.in, is a very young brand bieng run by 3 young entrepreneurs. We want to be become out of the league company delivering fabulous and beautiful serviced offices in India and abroad. We hire designers who have made spaces across the world. We want to get visiting card design which gives complete fresh look to the people who carries that card, has to be very impactful and should symbolise happy young and energetic brand. should be completely out of the box thinking of international level, should portray global brand image.

Target Market(s)

Startups, (Small, medium and large corporates)

Industry/Entity Type

Business

Contact Information for Business Card

Name, Email, Address, Mobile number, Landline number, website

Colors

Designer to choose colors to be used in the design.

Requirements
Must have
• Nice new shape
Nice to have
• We want creative cuts, different size and impactful brand clarity
Should not have
• Boring and regular design and shape

```html
<!DOCTYPE html>
<html lang="en">
<head>
<meta charset="UTF-8">
<title>Brevlo Business Card</title>
<link rel="stylesheet" href="https://fonts.googleapis.com/css2?family=Oswald:wght@500&family=Work+Sans:wght@400;500;600&display=swap">
<style>
  :root {
    --backdrop: #141414;
    --card: #262626;
    --card-edge: #323232;
    --accent: #e3161d;
    --text-light: #f2f2f2;
    --text-muted: #9a9a9a;
    --brand-silver: #c4c4c4;
  }
  * { box-sizing: border-box; margin: 0; padding: 0; }
  html, body {
    width: 1200px; height: 900px; overflow: hidden;
    background: var(--backdrop);
    font-family: "Work Sans", sans-serif;
  }
  .canvas { position: relative; width: 1200px; height: 900px; }
  .card-holder {
    position: absolute; left: 290px; width: 620px; height: 355px;
    filter: drop-shadow(0 12px 24px rgba(0,0,0,.6));
  }
  .card-holder--front { top: 60px; }
  .card-holder--back { top: 470px; }
  .card {
    position: relative; width: 100%; height: 100%;
    background: linear-gradient(135deg, var(--card-edge), var(--card));
    overflow: hidden;
  }
  .card--front {
    clip-path: polygon(0 0, 88% 0, 100% 18%, 100% 100%, 0 100%);
  }
  .card--back {
    clip-path: polygon(12% 0, 100% 0, 100% 100%, 0 100%, 0 18%);
  }
  .card__band {
    position: absolute; left: 0; right: 0; bottom: 0; height: 8px;
    background: var(--accent);
  }

  .brand {
    position: absolute; left: 0; right: 0; top: 138px;
    text-align: center;
    font-weight: 600; font-size: 60px; letter-spacing: 6px;
    color: var(--brand-silver); line-height: 1;
  }
  .website {
    position: absolute; left: 0; right: 0; bottom: 34px;
    text-align: center; font-size: 15px; letter-spacing: 1.5px;
    color: var(--text-light);
  }
  .website__domain { color: var(--accent); }

  .person {
    position: absolute; right: 330px; top: 122px; text-align: right;
  }
  .person__name {
    font-family: "Oswald", sans-serif; font-weight: 500;
    font-size: 42px; letter-spacing: 1px; line-height: 1;
    color: var(--accent); text-transform: uppercase; white-space: nowrap;
  }
  .person__role {
    margin-top: 10px; font-size: 17px; letter-spacing: 1px;
    color: var(--text-light); text-transform: uppercase;
  }
  .divider {
    position: absolute; left: 308px; top: 118px; width: 2px; height: 88px;
    background: var(--accent);
  }
  .contacts {
    position: absolute; left: 330px; top: 116px; list-style: none;
  }
  .contacts__item {
    display: flex; align-items: center; gap: 12px;
    font-size: 16px; letter-spacing: .5px; color: var(--text-light);
    height: 23px; white-space: nowrap;
  }
  .contacts__icon { width: 13px; height: 13px; fill: var(--accent); flex: none; }
  .location {
    position: absolute; left: 0; right: 0; bottom: 36px;
    text-align: center; font-size: 16px; letter-spacing: .5px;
    color: var(--text-light); white-space: nowrap;
  }
  .location__label { color: var(--accent); }
</style>
</head>
<body>
<main class="canvas">
  <div class="card-holder card-holder--front">
    <section class="card card--front">
      <p class="brand">BREVLO</p>
      <p class="website">www.<span class="website__domain">brevlo</span>.in</p>
      <div class="card__band"></div>
    </section>
  </div>

  <div class="card-holder card-holder--back">
    <section class="card card--back">
      <div class="person">
        <h1 class="person__name">Arjun Mehra</h1>
        <p class="person__role">Manager</p>
      </div>
      <div class="divider"></div>
      <ul class="contacts">
        <li class="contacts__item">
          <svg class="contacts__icon" viewBox="0 0 16 16"><path d="M4 0h8a1 1 0 0 1 1 1v14a1 1 0 0 1-1 1H4a1 1 0 0 1-1-1V1a1 1 0 0 1 1-1zm1 2v10h6V2zm3 11a1 1 0 1 0 0 2 1 1 0 0 0 0-2z"/></svg>
          (022) 481-3907
        </li>
        <li class="contacts__item">
          <svg class="contacts__icon" viewBox="0 0 16 16"><path d="M3.6 1l2.6 3-1.5 2c.9 2 2.3 3.4 4.3 4.3l2-1.5 3 2.6-1.5 2.6C6.8 14 2 9.2 1 2.5z"/></svg>
          (022) 615-2240
        </li>
        <li class="contacts__item">
          <svg class="contacts__icon" viewBox="0 0 16 16"><path d="M0 3h16v10H0zm1.5 1.3V12h13V4.3L8 9z"/></svg>
          arjun@brevlo.in
        </li>
        <li class="contacts__item">
          <svg class="contacts__icon" viewBox="0 0 16 16"><path d="M8 0a8 8 0 1 0 0 16A8 8 0 0 0 8 0zm0 2a6 6 0 0 1 5.7 4H10V4H6v3H3v3h3v4.7A6 6 0 0 1 8 2z"/></svg>
          brevlo.in
        </li>
      </ul>
      <p class="location"><span class="location__label">Location:</span> 46 Linking Road, Bandra West, Mumbai 400050</p>
      <div class="card__band"></div>
    </section>
  </div>
</main>
</body>
</html>
```